larkforge website

commerce website to sell cookeries, brackets, mailboxes and to show off homes built. Modern Steel in design see marlo cycles web page to be like: https://www.marlocycles-demo.com/en/ sorry its bright nest hosting word press divi

must be able to add products to page

Target Market(s)

mainly western states of U.S.

Industry/Entity Type

Building Product

Coding

Coded - Design and coding required

Number of Pages Required

3 page

Font styles to use
Sans Serif

Colors

Designer to choose colors to be used in the design.

Requirements
Must have
• customers to be able to order products from page
• bright nest hosting word press divi

```html
<!DOCTYPE html>
<html lang="en">
<head>
<meta charset="utf-8">
<title>Larkforge — Store</title>
<link href="https://fonts.googleapis.com/css2?family=Montserrat:wght@400;500;600;700&display=swap" rel="stylesheet">
<style>
:root{
  --navy:#414b78;
  --navy-dark:#323a60;
  --ink:#222;
  --muted:#777;
  --black:#1b1b1b;
  --grey-bg:#e0e0e0;
  --panel:#f1f1f1;
  --line:#e3e3e3;
  --star:#e9a928;
  --red:#d8232a;
  --white:#fff;
}
*{box-sizing:border-box;margin:0;padding:0}
html,body{width:697px;height:1200px;overflow:hidden;background:var(--grey-bg);font-family:"Montserrat",sans-serif;color:var(--ink)}
.stage{position:relative;width:1464px;height:2520px;transform:scale(0.47609);transform-origin:0 0}
.page{position:absolute;top:27px;width:686px;background:var(--white);overflow:hidden}
.page--home{left:31px;height:2466px}
.page--product{left:747px;height:1778px}
.sec{position:absolute;left:0;width:686px}
.abs{position:absolute}

/* header */
.topbar{top:0;height:22px;background:var(--black);color:#fff;font-size:8px;font-weight:600;display:flex;align-items:center;justify-content:center;gap:8px}
.topbar svg{width:20px;height:11px}
.header{top:22px;height:55px}
.brand{position:absolute;left:62px;top:20px;display:flex;align-items:center;gap:6px;font-size:15px;font-weight:600;color:var(--navy)}
.brand i{display:block;width:14px;height:14px;background:var(--navy);border-radius:50%}
.search{position:absolute;left:260px;top:14px;width:242px;height:28px;border:1px solid #ddd;border-radius:14px;display:flex;align-items:center;font-size:7px;color:#777;overflow:hidden}
.search span{padding-left:16px;width:118px}
.search span+span{border-left:1px solid #bbb;padding-left:12px}
.search b{margin-left:auto;width:34px;height:28px;background:var(--navy);display:flex;align-items:center;justify-content:center}
.acct{position:absolute;top:10px;font-size:7px;text-align:center;color:#333}
.acct svg{display:block;margin:0 auto 2px;width:22px;height:22px}
.nav{top:77px;height:29px;background:var(--navy);display:flex;align-items:center;justify-content:center;color:#fff;font-size:8.5px;font-weight:600}
.nav span{padding:0 18px;border-right:1px solid #fff;line-height:9px}
.nav span:last-child{border-right:0}

/* hero tiles */
.tile{position:absolute;color:#fff}
.tile small{display:block;font-size:8px;font-weight:600}
.tile h3{font-size:16px;font-weight:600}
.tile .pill{display:inline-block;margin-top:8px;background:var(--navy);border-radius:12px;padding:6px 14px;font-size:7px;font-weight:700}
.tile--firepit{background:radial-gradient(circle at 62% 28%,#c4692c 0,#6a4630 28%,#3a302b 55%,#26211e 100%)}
.tile--saferoom{background:linear-gradient(100deg,#8d9298 0,#3a3e45 38%,#1b1d22 70%,#2a2c31 100%)}
.tile--vault{background:linear-gradient(135deg,#2f3850 0,#161a25 55%,#6c6f78 100%)}
.tile--barn{background:linear-gradient(90deg,#141718 0,#3c4744 35%,#6a7a74 55%,#1c2021 100%)}

.offer{top:383px;height:36px;background:#5a5a5a;color:#fff;display:flex;align-items:center;font-size:10.5px}
.offer .tag{width:215px;height:36px;background:var(--navy);border-radius:0 18px 18px 0;display:flex;align-items:center;padding-left:110px;font-size:11.5px;font-weight:600}
.offer u{font-weight:600}
.textured{background:linear-gradient(180deg,#dcdcdc,#cfcfcf 50%,#dedede)}

/* titles */
.title{position:absolute;display:flex;align-items:center;gap:14px;font-size:16px;font-weight:700;text-transform:uppercase}
.title:after{content:"";flex:1;height:1px;background:var(--navy)}
.title.center:before{content:"";flex:1;height:1px;background:var(--navy)}
.arrows{position:absolute;display:flex;gap:3px}
.arrows i{width:18px;height:18px;border:1px solid #555;border-radius:50%;display:flex;align-items:center;justify-content:center;font-style:normal;font-size:10px}

/* product photo areas */
.shot{background:var(--sg)}
.shot--kettle{--sg:radial-gradient(ellipse 30% 44% at 50% 44%,#262626 0,#5c5c5c 45%,#cfcfcf 80%,#fff 100%)}
.shot--bowl{--sg:radial-gradient(ellipse 46% 30% at 50% 48%,#262626 0,#5a5a5a 45%,#d0d0d0 82%,#fff 100%)}
.shot--stand{--sg:radial-gradient(ellipse 42% 40% at 50% 40%,#242424 0,#5a5a5a 40%,#d2d2d2 82%,#fff 100%)}
.shot--table{--sg:radial-gradient(ellipse 46% 32% at 50% 55%,#2e3238 0,#6a5f52 45%,#d6d2cc 82%,#fff 100%)}
.shot--flame{--sg:radial-gradient(ellipse 46% 26% at 50% 45%,#3a2d26 0,#7a6a5e 45%,#d6d6d6 82%,#fff 100%)}
.shot--barrel{--sg:radial-gradient(ellipse 44% 36% at 50% 42%,#333 0,#7a7a7a 50%,#d8d8d8 84%,#fff 100%)}
.shot--kit{--sg:radial-gradient(ellipse 46% 32% at 50% 50%,#45453f 0,#85837c 50%,#dcdcda 84%,#fff 100%)}
.shot--dome{--sg:radial-gradient(ellipse 44% 34% at 50% 40%,#2a2a2a 0,#707070 48%,#d6d6d6 82%,#fff 100%)}

/* product card */
.pcard{position:absolute;width:133px;height:225px;background:#fff;display:flex;flex-direction:column;font-size:8.5px;text-align:center}
.pcard .head{display:flex;justify-content:space-between;padding:6px 5px 0;font-size:8px;color:#444}
.pcard .img{margin:4px 10px 0;height:112px}
.pcard p{margin-top:10px;line-height:13px;font-weight:500}
.pcard .price{font-size:11px;color:var(--navy);font-weight:600;margin-top:4px}
.pcard .bar{margin-top:auto;height:24px;background:var(--navy);color:#fff;display:flex;align-items:center;font-size:7.5px;font-weight:600}
.pcard .bar span{padding:0 5px;border-right:1px solid #7d85a8}
.pcard .bar b{flex:1;font-weight:600}

/* categories */
.cat{position:absolute;width:134px;height:101px;border:1px solid #ddd;background:#fff}
.cat svg{position:absolute;left:40px;top:8px;width:54px;height:54px}
.cat div{position:absolute;bottom:0;left:0;right:0;height:24px;background:var(--navy);color:#fff;font-size:8.5px;font-weight:700;display:flex;align-items:center;justify-content:center}
.circ{position:absolute;width:20px;height:20px;border:1px solid #444;border-radius:50%;font-size:10px;display:flex;align-items:center;justify-content:center}

/* brands */
.logo{position:absolute;width:140px;height:40px;display:flex;align-items:center;gap:6px;font-size:12px;font-weight:600;color:#333;white-space:nowrap}
.logo i{width:18px;height:18px;background:var(--navy);display:block;flex:none}

/* new card */
.ncard{position:absolute;width:131px;height:200px;background:#fff;border:1px solid #e2e2e2;text-align:center;font-size:9px}
.ncard .badge{position:absolute;left:10px;top:8px;width:22px;height:22px;border-radius:50%;background:var(--red)}
.ncard .img{margin:14px auto 0;width:90px;height:88px}
.ncard .stars{color:var(--star);font-size:11px;letter-spacing:1px;margin-top:4px}
.ncard .price{font-size:11px;font-weight:700;color:var(--navy);margin-top:3px}
.ncard p{margin-top:4px;line-height:13px;font-weight:500}
.ncard .go{margin:6px auto 0;width:18px;height:18px;border-radius:50%;background:#ddd;font-size:9px;line-height:18px}

/* signup */
.signup{background:var(--navy);color:#fff;text-align:center}
.signup h2{font-size:17px;font-weight:600;line-height:20px;padding-top:40px}
.signup form{margin:12px auto 0;width:266px;height:30px;background:#fff;border-radius:15px;display:flex;align-items:center;padding:2px;font-size:8px;color:#555}
.signup form span{flex:1;text-align:left;padding-left:18px}
.signup form b{background:var(--black);color:#fff;border-radius:13px;padding:8px 16px;font-size:7.5px}

/* footer */
.footer{background:#fbfbfb}
.fcol{position:absolute;top:30px;font-size:8px;color:#555}
.fcol h4{font-size:9px;font-weight:700;color:#222;margin-bottom:10px}
.fcol li{list-style:none;margin-bottom:9px;white-space:nowrap}
.fbrand{position:absolute;font-size:16px;font-weight:600;color:var(--navy)}
.cards{position:absolute;display:flex;gap:3px}
.cards i{width:22px;height:14px;border-radius:2px;display:block}
.copy{position:absolute;left:0;right:0;text-align:center;font-size:8px;color:#555}

/* product detail */
.gallery{position:absolute;left:62px;top:301px;width:275px;height:225px;border:1px solid #e5e5e5;background:#fafafa}
.thumb{position:absolute;left:8px;width:30px;height:26px;border:1px solid #ddd}
.info{position:absolute;left:370px;top:304px;width:250px;font-size:7.5px;line-height:14.6px;color:#666}
.info h1{font-size:11px;font-weight:600;color:#222;line-height:14px}
.info .sub{color:var(--navy);font-size:7.5px;margin-top:2px}
.info .pr{display:flex;align-items:center;gap:6px;margin:6px 0 4px;font-size:7.5px;color:#555}
.info .pr b{font-size:14px;color:var(--navy)}
.info .pr span{color:var(--star);font-size:9px}
.qty{display:flex;align-items:center;gap:10px;margin-top:10px;color:#222}
.qty .box{display:flex;align-items:center;border:1px solid #ccc;border-radius:10px;height:20px;font-size:9px}
.qty .box span{padding:0 6px}
.qty .box b{padding:0 10px;border:1px solid #ccc;height:20px;line-height:18px}
.qty .btn{margin-left:10px;background:var(--navy);color:#fff;border-radius:14px;padding:8px 13px;font-size:8.5px;font-weight:600}
.qa h3{font-size:10.5px;font-weight:700}
.field{position:absolute;border:1px solid #ddd;background:#fff;font-size:7.5px;color:#555}
</style>
</head>
<body>
<div class="stage">

<!-- HOME PAGE -->
<section class="page page--home">
  <div class="sec topbar"><svg viewBox="0 0 20 11"><rect x="0" y="1" width="12" height="7" fill="#fff"/><path d="M12 3h4l3 3v2h-7z" fill="#fff"/><circle cx="4" cy="9" r="1.6" fill="#fff"/><circle cx="15" cy="9" r="1.6" fill="#fff"/></svg>FREE SHIPPING OVER $50</div>
  <div class="sec header">
    <div class="brand"><i></i>LARKFORGE</div>
    <div class="search"><span>Search Products</span><span>All Categories</span><b><svg width="13" height="13" viewBox="0 0 13 13"><circle cx="5.5" cy="5.5" r="4" fill="none" stroke="#fff" stroke-width="1.4"/><path d="M8.5 8.5l3.5 3.5" stroke="#fff" stroke-width="1.4"/></svg></b></div>
    <div class="acct" style="left:530px"><svg viewBox="0 0 22 22"><circle cx="11" cy="7" r="5" fill="none" stroke="#333"/><path d="M2 21c1-6 17-6 18 0z" fill="none" stroke="#333"/></svg>My Account</div>
    <div class="acct" style="left:592px"><svg viewBox="0 0 22 22"><path d="M1 4h4l3 11h11l2-8H7" fill="none" stroke="#333"/><circle cx="9" cy="19" r="1.5" fill="#333"/><circle cx="17" cy="19" r="1.5" fill="#333"/></svg>My Cart</div>
  </div>
  <nav class="sec nav"><span>SHOP</span><span>LEARN</span><span>JOIN</span><span>DEALS</span><span>WHOLESALE</span><span>BECOME AFFILIATE</span><span>CONTACT</span></nav>

  <div class="tile tile--firepit" style="left:63px;top:131px;width:212px;height:227px" role="img" aria-label="Steel fire pit burning on a deck">
    <div style="position:absolute;left:15px;top:34px"><small>LARKFORGE</small><h3>FIREPIT</h3><span class="pill">SHOP NOW: ●</span></div>
  </div>
  <div class="tile tile--saferoom" style="left:282px;top:131px;width:204px;height:110px" role="img" aria-label="Open saferoom door">
    <div style="position:absolute;left:10px;top:8px"><h3 style="font-weight:500;font-size:12px">SAFEROOM</h3><span class="pill">SHOP NOW: ●</span></div>
  </div>
  <div class="tile tile--vault" style="left:282px;top:247px;width:204px;height:111px" role="img" aria-label="Vault door lock detail">
    <div style="position:absolute;left:10px;top:8px"><h3 style="font-weight:500;font-size:12px">VAULT</h3><span class="pill">SHOP NOW: ●</span></div>
  </div>
  <div class="tile tile--barn" style="left:492px;top:131px;width:130px;height:227px" role="img" aria-label="Steel barn doors">
    <div style="position:absolute;left:16px;top:14px"><h3 style="font-size:11.5px;line-height:14px">STEEL BARN<br>DOORS</h3><span class="pill">SHOP NOW: ●</span></div>
  </div>

  <div class="sec offer"><div class="tag">TODAY OFFER</div><span style="margin-left:32px">SALE .SAVE UP TO 20% ONLINE AND IN STORE . <u>SHOP ALL DEALS NOW</u></span></div>

  <div class="sec textured" style="top:419px;height:593px">
    <div class="title" style="left:63px;top:44px;width:560px">Top Sellers</div>
    <div class="pcard" style="left:63px;top:85px"><div class="head"><span># 0000</span><span>♡</span></div><div class="img shot shot--kettle" role="img" aria-label="Kettle grill"></div><p>Lorem ipsum dolor amet,<br>1244 consectetur</p><div class="price">$ 656.00</div><div class="bar"><span>−</span><span>1</span><span>+</span><b>ADD TO CART</b></div></div>
    <div class="pcard" style="left:204px;top:85px"><div class="head"><span># 0000</span><span>♡</span></div><div class="img shot shot--bowl" role="img" aria-label="Round fire pit with mesh lid"></div><p>Lorem ipsum dolor amet,<br>1244 consectetur</p><div class="price">$ 656.00</div><div class="bar"><span>−</span><span>1</span><span>+</span><b>ADD TO CART</b></div></div>
    <div class="pcard" style="left:346px;top:85px"><div class="head"><span># 0000</span><span>♡</span></div><div class="img shot shot--stand" role="img" aria-label="Fire bowl on stand"></div><p>Lorem ipsum dolor amet,<br>1244 consectetur</p><div class="price">$ 656.00</div><div class="bar"><span>−</span><span>1</span><span>+</span><b>ADD TO CART</b></div></div>
    <div class="pcard" style="left:487px;top:85px"><div class="head"><span># 0000</span><span>♡</span></div><div class="img shot shot--table" role="img" aria-label="Square fire table with logs"></div><p>Lorem ipsum dolor amet,<br>1244 consectetur</p><div class="price">$ 656.00</div><div class="bar"><span>−</span><span>1</span><span>+</span><b>ADD TO CART</b></div></div>
    <div class="pcard" style="left:63px;top:318px"><div class="head"><span># 0000</span><span>♡</span></div><div class="img shot shot--flame" role="img" aria-label="Fire pit with flames"></div><p>Lorem ipsum dolor amet,<br>1244 consectetur</p><div class="price">$ 656.00</div><div class="bar"><span>−</span><span>1</span><span>+</span><b>ADD TO CART</b></div></div>
    <div class="pcard" style="left:204px;top:318px"><div class="head"><span># 0000</span><span>♡</span></div><div class="img shot shot--barrel" role="img" aria-label="Charcoal grill with lid"></div><p>Lorem ipsum dolor amet,<br>1244 consectetur</p><div class="price">$ 656.00</div><div class="bar"><span>−</span><span>1</span><span>+</span><b>ADD TO CART</b></div></div>
    <div class="pcard" style="left:346px;top:318px"><div class="head"><span># 0000</span><span style="color:var(--navy)">♥</span></div><div class="img shot shot--kit" role="img" aria-label="Grill grate kit with wind guard"></div><p>Lorem ipsum dolor amet,<br>1244 consectetur</p><div class="price">$ 656.00</div><div class="bar"><span>−</span><span>1</span><span>+</span><b>ADD TO CART</b></div></div>
    <svg class="abs" style="left:538px;top:392px" width="32" height="32" viewBox="0 0 32 32" fill="#414b78"><circle cx="5" cy="5" r="4"/><circle cx="16" cy="5" r="4"/><circle cx="27" cy="5" r="4"/><circle cx="5" cy="16" r="4"/><circle cx="16" cy="16" r="4"/><circle cx="27" cy="16" r="4"/><circle cx="5" cy="27" r="4"/><circle cx="16" cy="27" r="4"/><circle cx="27" cy="27" r="4"/></svg>
    <div class="abs" style="left:491px;top:438px;width:125px;height:29px;border:1.5px solid var(--navy);border-radius:15px;font-size:8.5px;font-weight:600;color:var(--navy);display:flex;align-items:center;justify-content:center">VIEW ALL PRODUCTS</div>
  </div>

  <div class="sec" style="top:1012px;height:247px">
    <div class="title center" style="left:63px;top:45px;width:560px">Manufacturer Categories</div>
    <div class="circ" style="left:32px;top:126px">←</div><div class="circ" style="left:633px;top:126px">→</div>
    <div class="cat" style="left:63px;top:85px"><svg viewBox="0 0 54 54" fill="none" stroke="#414b78" stroke-width="3"><rect x="6" y="6" width="18" height="44"/><rect x="30" y="6" width="18" height="44"/><path d="M4 4h46"/></svg><div>STEEL BARN DOORS</div></div>
    <div class="cat" style="left:205px;top:85px"><svg viewBox="0 0 54 54" fill="#414b78"><path d="M27 4c6 10 14 14 12 26-1 6-6 8-12 8s-11-2-12-8c-1-8 6-10 6-18 4 4 5 7 6 10 2-6 0-12 0-18z"/><ellipse cx="27" cy="42" rx="22" ry="7"/></svg><div>FIRE PIT</div></div>
    <div class="cat" style="left:346px;top:85px"><svg viewBox="0 0 54 54" fill="none" stroke="#414b78" stroke-width="3"><rect x="14" y="6" width="34" height="38"/><path d="M6 6v38M2 10l4-4 4 4M2 40l4 4 4-4M14 50h34M30 20h12M30 30h12"/></svg><div>SAFEROOM</div></div>
    <div class="cat" style="left:487px;top:85px"><svg viewBox="0 0 54 54" fill="none" stroke="#414b78" stroke-width="3"><rect x="4" y="4" width="46" height="42"/><rect x="10" y="10" width="34" height="30"/><circle cx="27" cy="25" r="8"/><path d="M10 50h8M36 50h8"/></svg><div>VAULT</div></div>
  </div>

  <div class="sec" style="top:1259px;height:233px;background:var(--panel)">
    <div class="title center" style="left:63px;top:47px;width:560px">Top Brands</div>
    <div class="logo" style="left:63px;top:81px"><i></i>Norvale Labs</div>
    <div class="logo" style="left:218px;top:81px"><i></i>Quarry Co</div>
    <div class="logo" style="left:372px;top:81px"><i style="border-radius:50%"></i>Tallow Works</div>
    <div class="logo" style="left:500px;top:81px"><i style="border-radius:50%"></i>Brightline Group</div>
    <div class="logo" style="left:63px;top:144px"><i style="border-radius:50%"></i>Brightline Group</div>
    <div class="logo" style="left:218px;top:144px"><i style="border-radius:50%"></i>Tallow Works</div>
    <div class="logo" style="left:356px;top:144px"><i></i>Quarry Co</div>
    <div class="logo" style="left:513px;top:144px"><i></i>Norvale Labs</div>
  </div>

  <div class="sec" style="top:1492px;height:328px">
    <div class="title" style="left:63px;top:46px;width:510px">What's New</div>
    <div class="arrows" style="left:580px;top:46px"><i>←</i><i>→</i></div>
    <div class="ncard" style="left:63px;top:79px"><div class="badge"></div><div class="img shot shot--kettle" role="img" aria-label="Kettle grill with fire"></div><div class="stars">★★★★★</div><div class="price">$565</div><p>Lorem ipsum dolor sit<br>amet, 23333 elit, sed do</p><div class="go">›</div></div>
    <div class="ncard" style="left:206px;top:79px"><div class="badge"></div><div class="img shot shot--kettle" role="img" aria-label="Kettle grill"></div><div class="stars">★★★★★</div><div class="price">$565</div><p>Lorem ipsum dolor sit<br>amet, 23333 elit, sed do</p><div class="go">›</div></div>
    <div class="ncard" style="left:348px;top:79px"><div class="badge"></div><div class="img shot shot--dome" role="img" aria-label="Domed fire pit"></div><div class="stars">★★★★★</div><div class="price">$565</div><p>Lorem ipsum dolor sit<br>amet, 23333 elit, sed do</p><div class="go">›</div></div>
    <div class="ncard" style="left:491px;top:79px"><div class="badge"></div><div class="img shot shot--kettle" role="img" aria-label="Kettle grill"></div><div class="stars">★★★★★</div><div class="price">$565</div><p>Lorem ipsum dolor sit<br>amet, 23333 elit, sed do</p><div class="go">›</div></div>
  </div>

  <div class="sec" style="top:1820px;height:310px;background:var(--panel)">
    <div class="abs" style="left:66px;top:42px;width:202px;height:202px;border:1px solid #666;background:radial-gradient(circle at 45% 38%,#d0733a 0,#7a3b2c 30%,#5a3429 60%,#3a2a24 100%)" role="img" aria-label="Fire pit on a brick patio with chairs"></div>
    <div class="abs" style="left:199px;top:149px;width:126px;height:131px;border:1px solid #777"></div>
    <div class="abs" style="left:188px;top:135px;width:118px;height:108px;border:3px solid #fff;background:linear-gradient(135deg,#4a4a4a,#151515)" role="img" aria-label="Laser-cut steel panel detail"></div>
    <div class="abs" style="left:369px;top:76px;width:250px"><h2 style="font-size:16px;font-weight:700;padding:0 0 6px 32px;border-bottom:1px solid var(--navy);width:170px">WHO WE ARE</h2>
      <p style="margin-top:14px;font-size:7.6px;line-height:14.5px;color:#555">Lorem ipsum dolor sit amet, consectetur adipiscing elit, sed do eiusmod tempor incididunt ut labore et dolore magna aliqua. Quis ipsum suspendisse ultrices gravida. Risus commaecenas accumsan lacus vel facilisis. cididunt ut labore et dolore magna aliqua. Quis ipsum suspendisse ultrices gravida.</p>
      <span style="display:inline-block;margin-top:14px;margin-left:8px;background:var(--navy);color:#fff;border-radius:13px;padding:8px 16px;font-size:7.5px;font-weight:700">BUY NOW: ●</span></div>
  </div>

  <div class="sec signup" style="top:2130px;height:146px"><h2>SIGN UP FOR SPECIAL DEALS,<br>NEW PRODUCT ALERTS, AND MORE!</h2><form><span>Email Address</span><b>JOIN NOW!</b></form></div>

  <div class="sec footer" style="top:2276px;height:190px">
    <div class="fcol" style="left:63px"><h4>INFORMATION</h4><ul><li>About Us</li><li>Delivery Information</li><li>Privacy Policy</li><li>Terms &amp; Conditions</li><li>Contact</li><li>Shops</li></ul></div>
    <div class="fcol" style="left:178px"><h4>MY ACCOUNT</h4><ul><li>My Account</li><li>Order History</li><li>Wish List</li><li>Testimonials</li><li>Awards</li><li>Blog</li></ul></div>
    <div class="fcol" style="left:277px"><h4>CONTACT US</h4><ul><li>⌖ 418 Cedar Ridge Rd. #2</li><li>&nbsp;&nbsp;&nbsp;Mesa Verde, NM</li><li>✉ contact@larkforge.com</li><li>✆ +1 555-010-4821</li></ul></div>
    <div class="fcol" style="left:421px"><h4>FOLLOW US</h4><ul><li>Network</li><li>Gallery</li><li>Community</li><li>Updates</li></ul></div>
    <div class="fbrand" style="left:512px;top:62px">LARKFORGE</div>
    <div class="cards" style="left:513px;top:100px"><i style="background:#3a5ea8"></i><i style="background:#d23a2a"></i><i style="background:#2e7bc4"></i><i style="background:#e88a2a"></i></div>
    <div class="copy" style="top:170px">Copyright © 2020. All Rights Reserved</div>
  </div>
</section>

<!-- PRODUCT PAGE -->
<section class="page page--product">
  <div class="sec topbar"><svg viewBox="0 0 20 11"><rect x="0" y="1" width="12" height="7" fill="#fff"/><path d="M12 3h4l3 3v2h-7z" fill="#fff"/><circle cx="4" cy="9" r="1.6" fill="#fff"/><circle cx="15" cy="9" r="1.6" fill="#fff"/></svg>FREE SHIPPING OVER $50</div>
  <div class="sec header">
    <div class="brand"><i></i>LARKFORGE</div>
    <div class="search"><span>Search Products</span><span>All Categories</span><b><svg width="13" height="13" viewBox="0 0 13 13"><circle cx="5.5" cy="5.5" r="4" fill="none" stroke="#fff" stroke-width="1.4"/><path d="M8.5 8.5l3.5 3.5" stroke="#fff" stroke-width="1.4"/></svg></b></div>
    <div class="acct" style="left:530px"><svg viewBox="0 0 22 22"><circle cx="11" cy="7" r="5" fill="none" stroke="#333"/><path d="M2 21c1-6 17-6 18 0z" fill="none" stroke="#333"/></svg>My Account</div>
    <div class="acct" style="left:592px"><svg viewBox="0 0 22 22"><path d="M1 4h4l3 11h11l2-8H7" fill="none" stroke="#333"/><circle cx="9" cy="19" r="1.5" fill="#333"/><circle cx="17" cy="19" r="1.5" fill="#333"/></svg>My Cart</div>
  </div>
  <nav class="sec nav"><span>SHOP</span><span>LEARN</span><span>JOIN</span><span>DEALS</span><span>WHOLESALE</span><span>BECOME AFFILIATE</span><span>CONTACT</span></nav>
  <div class="sec" style="top:106px;height:146px;background:linear-gradient(180deg,#3e4348 0,#6b6860 35%,#7b776d 55%,#5b7a38 78%,#4a6a2c 100%)" role="img" aria-label="Stone patio with a lit fire pit at dusk"></div>

  <div class="gallery"><div class="thumb shot shot--bowl" style="top:10px"></div><div class="thumb shot shot--kettle" style="top:44px"></div>
    <div class="abs shot shot--kit" style="left:50px;top:20px;width:215px;height:190px" role="img" aria-label="Grill grate kit with wind guard"></div></div>
  <div class="info"><h1>Lorem ipsum dolor sit amet, consecteturing</h1><div class="sub">Ipsum suspendisse ultrices</div>
    <div class="pr"><b>$454</b><span>★★★★★</span>(124) Reviews</div>
    <p style="text-align:justify">Lorem ipsum dolor sit amet, consectetur adipiscing elit, sed do eiusmod tempor incididunt ut labore et dolore magna aliqua. Quis ipsum suspendisse ultrices gravida. Risus commodo viverra maecenas accumsan lacus vel facilisis. Lorem ipsum dolor sit amet, consectetur adipiscing elit, sed do eiusmod tempor incididunt ut labore et dolore magna aliqua. Quis ipsum suspendisse ultrices gravida. Risus commodo viverra maecenas accumsan lacus vel facilisis.</p>
    <div class="qty">Quantity <div class="box"><span>−</span><b>01</b><span>+</span></div><span class="btn">ADD TO CART</span></div></div>

  <div class="sec textured" style="top:575px;height:362px">
    <div class="title" style="left:67px;top:45px;width:510px">Products Related To This Item</div>
    <div class="arrows" style="left:580px;top:45px"><i>←</i><i>→</i></div>
    <div class="pcard" style="left:63px;top:85px"><div class="head"><span># 0000</span><span>♡</span></div><div class="img shot shot--kettle" role="img" aria-label="Kettle grill"></div><p>Lorem ipsum dolor amet,<br>1244 consectetur</p><div class="price">$ 656.00</div><div class="bar"><span>−</span><span>1</span><span>+</span><b>ADD TO CART</b></div></div>
    <div class="pcard" style="left:204px;top:85px"><div class="head"><span># 0000</span><span>♡</span></div><div class="img shot shot--bowl" role="img" aria-label="Round fire pit with mesh lid"></div><p>Lorem ipsum dolor amet,<br>1244 consectetur</p><div class="price">$ 656.00</div><div class="bar"><span>−</span><span>1</span><span>+</span><b>ADD TO CART</b></div></div>
    <div class="pcard" style="left:346px;top:85px"><div class="head"><span># 0000</span><span>♡</span></div><div class="img shot shot--stand" role="img" aria-label="Fire bowl on stand"></div><p>Lorem ipsum dolor amet,<br>1244 consectetur</p><div class="price">$ 656.00</div><div class="bar"><span>−</span><span>1</span><span>+</span><b>ADD TO CART</b></div></div>
    <div class="pcard" style="left:487px;top:85px"><div class="head"><span># 0000</span><span>♡</span></div><div class="img shot shot--table" role="img" aria-label="Square fire table with logs"></div><p>Lorem ipsum dolor amet,<br>1244 consectetur</p><div class="price">$ 656.00</div><div class="bar"><span>−</span><span>1</span><span>+</span><b>ADD TO CART</b></div></div>
  </div>

  <div class="sec qa" style="top:937px;height:506px">
    <h3 class="abs" style="left:63px;top:48px">CUSTOMER QUESTIONS &amp; ANSWERS</h3>
    <div class="field" style="left:63px;top:75px;width:248px;height:28px;border-radius:14px;padding:9px 12px">Have a question? Search for answer</div>
    <div class="abs" style="left:64px;top:120px;font-size:8px;line-height:15px">Typical questions asked about products:<br>&nbsp;-&nbsp; Is the item durable?<br>&nbsp;-&nbsp; Is this item easy to use?<br>&nbsp;-&nbsp; What are the dimensions of this item?</div>
    <h3 class="abs" style="left:362px;top:48px">NO CUSTOMER REVIEWS</h3>
    <div class="abs" style="left:362px;top:68px;color:var(--star);font-size:24px;letter-spacing:1px">★★★★★</div>
    <div class="abs" style="left:494px;top:72px;background:var(--navy);color:#fff;border-radius:13px;padding:8px 16px;font-size:8.5px;font-weight:600">Write a product review</div>
    <div class="field" style="left:362px;top:106px;width:260px;height:70px;padding:8px">Message</div>
    <div class="title" style="left:64px;top:226px;width:510px">What's New</div>
    <div class="arrows" style="left:580px;top:226px"><i>←</i><i>→</i></div>
    <div class="ncard" style="left:63px;top:259px"><div class="badge"></div><div class="img shot shot--kettle" role="img" aria-label="Kettle grill with fire"></div><div class="stars">★★★★★</div><div class="price">$565</div><p>Lorem ipsum dolor sit<br>amet, 23333 elit, sed do</p><div class="go">›</div></div>
    <div class="ncard" style="left:206px;top:259px"><div class="badge"></div><div class="img shot shot--kettle" role="img" aria-label="Kettle grill"></div><div class="stars">★★★★★</div><div class="price">$565</div><p>Lorem ipsum dolor sit<br>amet, 23333 elit, sed do</p><div class="go">›</div></div>
    <div class="ncard" style="left:348px;top:259px"><div class="badge"></div><div class="img shot shot--dome" role="img" aria-label="Domed fire pit"></div><div class="stars">★★★★★</div><div class="price">$565</div><p>Lorem ipsum dolor sit<br>amet, 23333 elit, sed do</p><div class="go">›</div></div>
    <div class="ncard" style="left:491px;top:259px"><div class="badge"></div><div class="img shot shot--kettle" role="img" aria-label="Kettle grill"></div><div class="stars">★★★★★</div><div class="price">$565</div><p>Lorem ipsum dolor sit<br>amet, 23333 elit, sed do</p><div class="go">›</div></div>
  </div>

  <div class="sec signup" style="top:1443px;height:146px"><h2>SIGN UP FOR SPECIAL DEALS,<br>NEW PRODUCT ALERTS, AND MORE!</h2><form><span>Email Address</span><b>JOIN NOW!</b></form></div>

  <div class="sec footer" style="top:1589px;height:189px">
    <div class="fcol" style="left:63px"><h4>INFORMATION</h4><ul><li>About Us</li><li>Delivery Information</li><li>Privacy Policy</li><li>Terms &amp; Conditions</li><li>Contact</li><li>Shops</li></ul></div>
    <div class="fcol" style="left:178px"><h4>MY ACCOUNT</h4><ul><li>My Account</li><li>Order History</li><li>Wish List</li><li>Testimonials</li><li>Awards</li><li>Blog</li></ul></div>
    <div class="fcol" style="left:277px"><h4>CONTACT US</h4><ul><li>⌖ 418 Cedar Ridge Rd. #2</li><li>&nbsp;&nbsp;&nbsp;Mesa Verde, NM</li><li>✉ contact@larkforge.com</li><li>✆ +1 555-010-4821</li></ul></div>
    <div class="fcol" style="left:421px"><h4>FOLLOW US</h4><ul><li>Network</li><li>Gallery</li><li>Community</li><li>Updates</li></ul></div>
    <div class="fbrand" style="left:512px;top:62px">LARKFORGE</div>
    <div class="cards" style="left:513px;top:100px"><i style="background:#3a5ea8"></i><i style="background:#d23a2a"></i><i style="background:#2e7bc4"></i><i style="background:#e88a2a"></i></div>
    <div class="copy" style="top:170px">Copyright © 2020. All Rights Reserved</div>
  </div>
</section>

</div>
</body>
</html>
```